Australian Trucking Company Requires Professional Looking Stationary

We require a professional looking stationary design that incorporates our newly designed logo.

Our business, called "Brell Haulage Contracting", provides contracting work, transport and logistics to business in Western Australia particularly with links to the mining sector.

We are a small business looking to expand and our new logo and our new stationary will help develop our brand image in our market place.

Target Market(s)

Businesses and Corporation with links to the Mining Sector

Industry/Entity Type

Small Business

Requirements
Must have
• The letterhead must have the following details:
The new logo

Text saying: "Brell Holdings Pty Ltd (ACN 582 316 907) ATF The Brell Discretionary Trust T/AS"
"ABN 71 834 209 553"
Address "P.O Box 817 Wattlegrove WA, 6958"
Phone: 08 9352 7140
Email: brellhaul@mailbox-example.com.au

The text on the letterhead should be editable as the details are likely to change in the near future. Provision should be made for a website address all though one isn't available at the moment.

The styling, layout and font text is entirely up to the designer.

```html
<!DOCTYPE html>
<html lang="en">
<head>
<meta charset="utf-8">
<title>Brell Haulage Contracting – Business Card</title>
<link href="https://fonts.googleapis.com/css2?family=Open+Sans:wght@400;600;700&display=swap" rel="stylesheet">
<style>
  :root {
    --backdrop: #e8e5e1;
    --card: #ffffff;
    --red: #d4202c;
    --red-dark: #a5141d;
    --charcoal: #2e3133;
    --text: #333333;
    --muted: #555555;
  }
  * { margin: 0; padding: 0; box-sizing: border-box; }
  html, body {
    width: 1200px; height: 426px; overflow: hidden;
    background: var(--backdrop);
    font-family: "Open Sans", Arial, sans-serif;
    color: var(--text);
  }
  .stage { position: relative; width: 1200px; height: 426px; }
  .card {
    position: absolute; top: 42px; width: 520px; height: 298px;
    background: var(--card); border-radius: 20px; overflow: hidden;
    box-shadow: 0 4px 10px rgba(0,0,0,.18);
  }
  .card--front { left: 62px; }
  .card--back { left: 606px; }

  .brand {
    position: absolute; left: 38px; top: 34px;
    display: flex; align-items: flex-start; gap: 14px;
  }
  .brand__mark { width: 22px; height: 22px; background: var(--red); margin-top: 6px; }
  .brand__name {
    color: var(--red); font-weight: 700; font-size: 30px;
    line-height: 34px; text-transform: uppercase; letter-spacing: .5px;
  }

  .person { position: absolute; left: 23px; top: 150px; font-size: 17px; font-weight: 700; }
  .person__role { font-size: 13px; font-weight: 400; }

  .contact-band {
    position: absolute; left: 0; top: 176px; width: 445px; height: 37px;
    background: linear-gradient(90deg, var(--red-dark), var(--red) 40%, var(--red));
    display: flex; align-items: center; gap: 12px; padding-left: 20px;
    color: #fff; font-size: 13px;
  }
  .contact-band__item { display: flex; align-items: center; gap: 4px; white-space: nowrap; }
  .contact-band__item svg { width: 12px; height: 12px; fill: #fff; }
  .contact-band__end {
    position: absolute; left: 445px; top: 176px; width: 75px; height: 37px;
    background: linear-gradient(90deg, var(--charcoal), #5a5d60);
  }
  .truck-art {
    position: absolute; left: 414px; top: 128px; width: 78px; height: 88px;
    border-radius: 8px;
    background: linear-gradient(135deg, var(--charcoal), var(--red-dark));
  }

  .address {
    position: absolute; right: 80px; top: 222px; font-size: 13px;
    display: flex; align-items: center; gap: 4px; white-space: nowrap;
  }
  .address svg { width: 10px; height: 10px; fill: var(--red); }
  .legal {
    position: absolute; left: 34px; right: 80px; top: 254px;
    font-size: 10px; line-height: 17px; color: var(--muted);
  }
  .legal p { white-space: nowrap; }
  .legal__abn { text-align: right; }

  .back-brand {
    position: absolute; inset: 0; display: flex; align-items: center; justify-content: center;
    color: var(--red); font-weight: 700; font-size: 34px; line-height: 40px;
    text-transform: uppercase; text-align: center;
  }
</style>
</head>
<body>
<main class="stage">
  <section class="card card--front" aria-label="Business card front">
    <div class="brand">
      <span class="brand__mark"></span>
      <div class="brand__name">Brell<br>Haulage<br>Contracting</div>
    </div>

    <p class="person">Persons name, <span class="person__role">Manager</span></p>

    <div class="contact-band">
      <span class="contact-band__item">
        <svg viewBox="0 0 16 16"><path d="M3.6 1.2l2.3 2.6-1.3 2a9 9 0 0 0 5.6 5.6l2-1.3 2.6 2.3-1.3 2.2C6.9 16 0 9.1 1.4 2.5z"/></svg>
        08 9352 7140
      </span>
      <span class="contact-band__item">
        <svg viewBox="0 0 16 16"><path d="M1 3h14v10H1zm1.5 1.4v.3L8 8.6l5.5-3.9v-.3zM2.5 6.4v5.1h11V6.4L8 10.3z"/></svg>
        brellhaul@mailbox-example.com.au
      </span>
    </div>
    <div class="contact-band__end"></div>
    <div class="truck-art" role="img" aria-label="Illustration of a truck driving forward"></div>

    <p class="address">
      <svg viewBox="0 0 10 10"><path d="M5 0l5 5H8.5v5h-2.5V7H4v3H1.5V5H0z"/></svg>
      P.O Box 817 Wattlegrove WA, 6958
    </p>
    <div class="legal">
      <p>Brell Holdings Pty Ltd (ACN 582 316 907) ATF The Brell Discretionary Trust T/AS</p>
      <p class="legal__abn">ABN 71 834 209 553</p>
    </div>
  </section>

  <section class="card card--back" aria-label="Business card back">
    <div class="back-brand">Brell<br>Haulage<br>Contracting</div>
  </section>
</main>
</body>
</html>
```